Business Card Design Project

We are rebranding an existing automotive collision repair business. The business is called dent haven. I have attached logo but I'm not tied to that. I want to leave this wide open.

I want this card to say we are professional, competent, cutting edge. We are focused on customers and use a lot of the latest technology to make the customer experience different. We sign customers in on iPads. Paperwork I signed electronically and updates are sent via text, email, logging on a website or as they wish. I want this innovation and image to come through in our cards

Target Market(s)

60%. Women 40% men. Age 35-60

Industry/Entity Type

Automotive

Requirements
Must have
• The card must have name, title, phone,email, cell, web page

```html
<!DOCTYPE html>
<html lang="en">
<head>
<meta charset="utf-8">
<title>dent haven — Business Card</title>
<link href="https://fonts.googleapis.com/css2?family=Open+Sans:wght@400;600;800&display=swap" rel="stylesheet">
<style>
  :root {
    --page: #e9e9e7;
    --card-top: #4a4b4d;
    --card-bottom: #2b2c2e;
    --green: #8cc63f;
    --text-light: #f2f2f2;
    --text-muted: #b9bbbd;
  }
  * { box-sizing: border-box; margin: 0; padding: 0; }
  html, body { width: 851px; height: 1200px; overflow: hidden; }
  body {
    background: var(--page);
    font-family: "Open Sans", Arial, sans-serif;
    position: relative;
  }
  .card {
    position: absolute;
    top: 302px;
    width: 340px;
    height: 596px;
    border-radius: 6px;
    overflow: hidden;
    background: linear-gradient(160deg, var(--card-top), var(--card-bottom) 70%);
    box-shadow: 0 6px 18px rgba(0,0,0,0.22);
  }
  .card--front { left: 70px; }
  .card--back { left: 441px; }
  .card__band { position: absolute; left: 0; top: 0; width: 340px; height: 596px; }

  .wordmark {
    position: absolute;
    font-weight: 800;
    color: var(--green);
    letter-spacing: -0.5px;
    white-space: nowrap;
  }
  .card--front .wordmark { left: 26px; top: 42px; font-size: 30px; }
  .card--back .wordmark { right: 26px; top: 390px; font-size: 34px; }

  .identity { position: absolute; left: 26px; top: 300px; }
  .identity__name { color: var(--text-light); font-weight: 600; font-size: 21px; }
  .identity__title { color: var(--green); font-size: 12px; margin-top: 2px; letter-spacing: 0.5px; }

  .contacts { position: absolute; left: 26px; top: 430px; list-style: none; }
  .contacts li {
    display: flex; align-items: center; gap: 10px;
    color: var(--text-muted); font-size: 12.5px; line-height: 24px;
  }
  .contacts svg { width: 12px; height: 12px; flex: none; }

  .web { position: absolute; right: 26px; top: 442px; color: var(--text-muted); font-size: 13px; }
</style>
</head>
<body>

  <section class="card card--front" aria-label="Card front">
    <svg class="card__band" viewBox="0 0 340 596" aria-hidden="true">
      <defs>
        <linearGradient id="silverFront" x1="0" y1="0" x2="1" y2="1">
          <stop offset="0" stop-color="#f4f4f4"/>
          <stop offset="1" stop-color="#a6a8aa"/>
        </linearGradient>
      </defs>
      <path d="M0 0 H340 V40 C260 70 170 120 0 150 Z" fill="url(#silverFront)"/>
      <path d="M0 150 C170 120 260 70 340 40 V52 C260 84 170 132 0 162 Z" fill="#8cc63f"/>
      <path d="M0 162 C170 132 260 84 340 52 V58 C260 92 170 140 0 168 Z" fill="#3c3d3f" opacity="0.6"/>
    </svg>
    <div class="wordmark">dent haven</div>

    <div class="identity">
      <div class="identity__name">Nate Carver</div>
      <div class="identity__title">Managing Director</div>
    </div>

    <ul class="contacts">
      <li><svg viewBox="0 0 12 12"><path d="M3 1 L5 3 L4 5 Q5 7 7 8 L9 7 L11 9 L9 11 Q4 10 1 3 Z" fill="#8cc63f"/></svg>t. 555 0142 7781</li>
      <li><svg viewBox="0 0 12 12"><rect x="3" y="1" width="6" height="10" rx="1" fill="#8cc63f"/></svg>c. 555 0142 7782</li>
      <li><svg viewBox="0 0 12 12"><rect x="1" y="4" width="10" height="5" fill="#8cc63f"/><rect x="3" y="1" width="6" height="3" fill="#8cc63f"/></svg>f. 555 0142 7783</li>
      <li><svg viewBox="0 0 12 12"><rect x="1" y="2.5" width="10" height="7" fill="#8cc63f"/><path d="M1 2.5 L6 7 L11 2.5" stroke="#2b2c2e" fill="none"/></svg>info@denthaven.com</li>
      <li><svg viewBox="0 0 12 12"><circle cx="6" cy="6" r="5" fill="#8cc63f"/></svg>www.denthaven.com</li>
    </ul>
  </section>

  <section class="card card--back" aria-label="Card back">
    <svg class="card__band" viewBox="0 0 340 596" aria-hidden="true">
      <path d="M0 0 H340 V250 C230 290 120 320 0 330 Z" fill="#5a5b5d" opacity="0.5"/>
    </svg>
    <div class="wordmark">dent haven</div>
    <div class="web">www.denthaven.com</div>
  </section>

</body>
</html>
```